Website for software company "velora"

We need a website for our software company/startup named "velora". We are developing several products (currently 3 standard-software products) which are all in different sectors, but all our products are available for Laptops/PC/Mobile Phones/Tablets, ... We do also create custom software and support our customers with consulting to optimize their processes.
We already have a Logo which you can find in the attached files.
We are a young team of 4 members (two founders and 2 employees).

To get an idea of our products -> the first one is a planning software for healthcare organizations (eg. BlueHaven, firebrigade, pharmacy), the second one is a booking software for sport clubs and the third one is a competition software for sports hunting. You see very diverse. Include or ignore this info of our products as you like.

The design has to be a bootstrap 4 (or higher) design. We have licenced FontAwesome as iconset. Responsive design should come without saying.

• Starting page, product pages, news section, contact, team, services

```html
<!DOCTYPE html>
<html lang="en">
<head>
<meta charset="utf-8">
<title>velora – Software for every sector</title>
<link href="https://fonts.googleapis.com/css2?family=Montserrat:wght@500;600;700&family=Lato:wght@400;700&display=swap" rel="stylesheet">
<style>
:root{
  --orange:#f47e2f;
  --orange-dark:#e86d1c;
  --ink:#222832;
  --text:#3d4049;
  --muted:#5c5f66;
  --white:#ffffff;
  --soft:#eef3fa;
  --field:#eef2f7;
  --footer:#262b34;
}
*{box-sizing:border-box;margin:0;padding:0}
html,body{width:1200px;height:3383px;overflow:hidden}
body{position:relative;font-family:'Lato',sans-serif;color:var(--text);background:var(--white)}
.abs{position:absolute}
a{color:inherit;text-decoration:none}

/* top bar */
.topbar{left:0;top:0;width:1200px;height:41px;background:var(--orange);color:var(--white);font-size:14px}
.social{left:111px;top:9px;display:flex;gap:12px}
.social span{width:24px;height:24px;border:1.5px solid var(--ink);border-radius:50%;display:block}
.contact-mini{top:12px;display:flex;align-items:center;gap:8px;color:var(--white)}
.contact-mini b{font-weight:700}

/* nav */
.nav{left:0;top:41px;width:1200px;height:85px;background:var(--white)}
.logo{font-family:'Montserrat',sans-serif;font-weight:600;font-size:46px;letter-spacing:1px;color:var(--ink);display:flex;align-items:center;gap:10px}
.logo i{width:16px;height:16px;background:var(--orange);display:block}
.nav .logo{left:110px;top:16px}
.menu{left:453px;top:31px;display:flex;gap:0;font-size:17px;color:var(--text)}
.menu a{margin-right:27px}
.btn{display:flex;align-items:center;justify-content:center;background:var(--orange);color:var(--white);font-weight:700;font-size:17px;border-radius:25px}
.nav .btn{left:956px;top:17px;width:132px;height:50px}

/* hero */
.hero{left:0;top:126px;width:1200px;height:617px;background:linear-gradient(100deg,#6a4a33 0%,#3a3431 45%,#1d2c40 70%,#14223a 100%)}
.hero-shade{left:0;top:0;width:567px;height:617px;background:linear-gradient(135deg,rgba(244,126,47,.35) 0%,rgba(244,126,47,.15) 60%,rgba(0,0,0,0) 100%)}
.hero h1{left:658px;top:170px;font-family:'Montserrat',sans-serif;font-weight:700;font-size:46px;color:var(--white)}
.hero .rule{left:658px;top:234px;width:210px;height:2px;background:var(--orange)}
.hero p{left:658px;top:280px;width:460px;font-size:17px;line-height:30px;font-weight:700;color:var(--white)}
.hero .btn{left:658px;top:393px;width:132px;height:50px}
.dots{left:1147px;top:253px;display:flex;flex-direction:column;gap:17px}
.dots span{width:8px;height:8px;border-radius:50%;background:var(--white)}
.dots span.on{width:11px;height:11px;margin-left:-1.5px;background:var(--orange)}

/* section titles */
.title{width:1200px;left:0;text-align:center;font-family:'Montserrat',sans-serif;font-weight:600;font-size:44px;color:var(--ink)}
.title em{font-style:normal;color:var(--orange)}

/* software cards */
.card{width:311px;height:391px;top:910px;background:var(--white);box-shadow:0 2px 10px rgba(0,0,0,.14);text-align:center}
.card .photo{width:311px;height:217px}
.card .icon{position:absolute;left:109px;top:151px;width:92px;height:92px;border:2px solid var(--orange);border-radius:14px;background:var(--white);display:flex;align-items:center;justify-content:center}
.card .icon div{width:78px;height:78px;border-radius:10px;box-shadow:0 1px 6px rgba(0,0,0,.2);display:flex;align-items:center;justify-content:center}
.card h3{margin-top:50px;font-family:'Montserrat',sans-serif;font-weight:600;font-size:19px;color:var(--ink)}
.card p{margin:15px auto 0;width:280px;font-size:16px;line-height:30px;color:var(--muted)}

/* about */
.about{left:0;top:1393px;width:1200px;height:542px;background:var(--orange)}
.about h2{left:112px;top:70px;font-family:'Montserrat',sans-serif;font-weight:700;font-size:46px;color:var(--white)}
.about p{left:112px;top:142px;width:565px;font-size:16.5px;line-height:30.2px;color:var(--white)}
.btn-outline{left:112px;top:415px;width:135px;height:51px;border:2px solid var(--white);border-radius:26px;color:var(--white);font-weight:700;font-size:17px;display:flex;align-items:center;justify-content:center}
.frame{left:729px;top:59px;width:346px;height:300px;border:2px solid var(--white);border-bottom:none}

/* news */
.news{width:316px;top:2099px}
.news .photo{width:316px;height:250px}
.news .body{position:absolute;left:8px;top:232px;width:300px;height:231px;background:var(--white);box-shadow:0 2px 10px rgba(0,0,0,.12);padding:30px 0 0 20px}
.news .meta{font-family:'Montserrat',sans-serif;font-size:14px;color:var(--orange)}
.news h4{margin-top:18px;font-family:'Montserrat',sans-serif;font-weight:600;font-size:16.5px;color:var(--ink)}
.news p{margin-top:14px;font-family:'Montserrat',sans-serif;font-size:16.5px;line-height:30px;color:var(--text)}

/* contact */
.contact{left:0;top:2638px;width:1200px;height:483px;background:var(--soft)}
.contact h2{left:110px;top:62px;font-family:'Montserrat',sans-serif;font-weight:700;font-size:44px;color:var(--ink)}
.contact h2 em{font-style:normal;color:var(--orange)}
.contact .lead{left:112px;top:138px;width:470px;font-size:16.5px;line-height:30px}
.info{left:112px;display:flex;align-items:center;gap:22px;font-family:'Montserrat',sans-serif;font-size:16.5px;color:var(--ink)}
.info svg{width:28px;height:32px}
.form{left:610px;top:52px;width:478px;height:361px;background:var(--white);box-shadow:0 2px 10px rgba(0,0,0,.1)}
.form h5{position:absolute;left:39px;top:28px;font-size:17px;font-weight:700;color:var(--ink)}
.field{position:absolute;background:var(--field);font-size:13px;color:#777;padding:14px 0 0 20px}
.form .btn{position:absolute;left:40px;top:283px;width:132px;height:48px}

/* footer */
.footer{left:0;top:3121px;width:1200px;height:262px;background:var(--footer);color:var(--white);text-align:center}
.footer .logo{position:absolute;left:0;width:1200px;top:44px;justify-content:center;color:var(--white)}
.foot-menu{position:absolute;left:0;width:1200px;top:124px;display:flex;justify-content:center;gap:40px;font-family:'Montserrat',sans-serif;font-weight:600;font-size:17px}
.copy{position:absolute;left:0;width:1200px;top:166px;font-family:'Montserrat',sans-serif;font-size:16px}
</style>
</head>
<body>

<header class="abs topbar">
  <div class="abs social"><span></span><span></span><span></span></div>
  <div class="abs contact-mini" style="left:676px">
    <svg width="16" height="16" viewBox="0 0 24 24"><path fill="#222832" d="M6.6 10.8c1.4 2.8 3.8 5.1 6.6 6.6l2.2-2.2c.3-.3.7-.4 1-.2 1.1.4 2.3.6 3.6.6.6 0 1 .4 1 1V20c0 .6-.4 1-1 1C10.6 21 3 13.4 3 4c0-.6.4-1 1-1h3.5c.6 0 1 .4 1 1 0 1.3.2 2.5.6 3.6.1.3 0 .7-.2 1z"/></svg>
    <span><b>Call:</b> +1 555-014-2290</span>
  </div>
  <div class="abs contact-mini" style="left:898px">
    <svg width="18" height="14" viewBox="0 0 24 18"><path fill="#222832" d="M0 0h24v18H0z"/><path fill="none" stroke="#f47e2f" stroke-width="2" d="M1 1l11 9 11-9"/></svg>
    <span><b>Email:</b> info@velora.com</span>
  </div>
</header>

<nav class="abs nav">
  <div class="abs logo"><i></i>VELORA</div>
  <div class="abs menu"><a>Home</a><a>About</a><a>Services</a><a>Our Project</a><a>Blog</a><a>Contact</a></div>
  <a class="abs btn">Get a Quote</a>
</nav>

<section class="abs hero" role="img" aria-label="Two developers working together at a desktop monitor showing app screens">
  <div class="abs hero-shade"></div>
  <h1 class="abs">Welcome To VELORA</h1>
  <div class="abs rule"></div>
  <p class="abs">Sed ut perspiciatis unde omnis iste natus error st volupm accusantium doloremque laudantium, totam rem apriam, eaque ipsa quae ab illo inventore veritatis et quasi.</p>
  <a class="abs btn">Get a Quote</a>
  <div class="abs dots"><span></span><span></span><span class="on"></span><span></span><span></span></div>
</section>

<h2 class="abs title" style="top:808px">Our <em>Software</em></h2>

<article class="abs card" style="left:112px">
  <div class="photo" role="img" aria-label="Doctor reviewing a tablet in a clinic" style="background:linear-gradient(135deg,#e9eef2,#c9d3da)"></div>
  <div class="icon"><div><svg width="46" height="40" viewBox="0 0 46 40"><path fill="none" stroke="#f47e2f" stroke-width="2" d="M23 36S4 24 4 13a9 9 0 0 1 19-4 9 9 0 0 1 19 4c0 3-1 6-3 8"/><path fill="none" stroke="#333" stroke-width="2" d="M6 20h8l3-5 4 9 3-4h6"/><circle cx="36" cy="26" r="6" fill="none" stroke="#333" stroke-width="2"/><path stroke="#333" stroke-width="2" d="M36 22v8M32 26h8"/></svg></div></div>
  <h3>Healthcare Organizations</h3>
  <p>Ut enim ad minima veniam, nostrum exercitationem ullam corporis.</p>
</article>
<article class="abs card" style="left:444px">
  <div class="photo" role="img" aria-label="Young footballer kicking a ball on a training pitch" style="background:linear-gradient(180deg,#e4e7ea 0%,#b8c4c8 55%,#5e8a3d 60%,#3f6f2a 100%)"></div>
  <div class="icon"><div><svg width="46" height="46" viewBox="0 0 46 46"><circle cx="20" cy="20" r="14" fill="none" stroke="#333" stroke-width="2"/><path fill="none" stroke="#333" stroke-width="2" d="M6 20h28M20 6v28M10 10c6 6 14 6 20 0M10 30c6-6 14-6 20 0"/><ellipse cx="31" cy="33" rx="10" ry="6" fill="#fff" stroke="#f47e2f" stroke-width="2"/><path stroke="#f47e2f" stroke-width="2" d="M26 33h10M28 31v4M31 31v4M34 31v4"/></svg></div></div>
  <h3>Sport Clubs</h3>
  <p>Ut enim ad minima veniam, nostrum exercitationem ullam corporis.</p>
</article>
<article class="abs card" style="left:776px">
  <div class="photo" role="img" aria-label="Hunter in an orange vest in open grassland" style="background:linear-gradient(180deg,#c8ccd0 0%,#a9a6a0 50%,#8a7457 60%,#6d5a41 100%)"></div>
  <div class="icon"><div><svg width="44" height="44" viewBox="0 0 44 44"><circle cx="22" cy="22" r="18" fill="none" stroke="#333" stroke-width="2"/><circle cx="22" cy="22" r="12" fill="none" stroke="#f47e2f" stroke-width="2"/><path fill="none" stroke="#333" stroke-width="2" d="M14 24l8-6 8 2-6 6zM22 4v6M22 34v6M4 22h6M34 22h6"/></svg></div></div>
  <h3>Sports Hunting</h3>
  <p>Ut enim ad minima veniam, nostrum exercitationem ullam corporis.</p>
</article>

<section class="abs about">
  <h2 class="abs">About Us</h2>
  <p class="abs">Sed ut perspiciatis unde omnis iste natus error sit voluptatem accusantium doloremque laudantium, totam rem aperiam, eaque ipsa quaeillo inventore veritatis et quasi architecto beatae vitae dicta sunt explicabo. Nemo enimg ipsam voluptatem quia voluptas sit aspernatur aut odit aut fugit, sed quiagj consequuntur magni dolores eos qui ratione voluptatem sequi nesciunt. Neque porro quisquam est, qui dolorem ipsum quia dolor sit aconsectetur, adipisci velit, sed quia non numquam eius modi tempora incidunt ut labore et dolore magnam aliquam quaerat voluptatem.</p>
  <a class="abs btn-outline">Get a Quote</a>
  <div class="abs frame"></div>
  <div class="abs" role="img" aria-label="Two colleagues discussing work at a computer monitor" style="left:743px;top:71px;width:345px;height:344px;background:linear-gradient(135deg,#8f9ba6,#d7dde2 60%,#f2f2f2)"></div>
  <div class="abs" role="img" aria-label="Developer looking at code on a monitor" style="left:697px;top:373px;width:258px;height:121px;background:linear-gradient(90deg,#c7c2bd,#e9e8e6 50%,#3a3f48)"></div>
</section>

<h2 class="abs title" style="top:2000px">Latest <em>News</em></h2>

<article class="abs news" style="left:112px">
  <div class="photo" role="img" aria-label="Team sketching ideas on a whiteboard" style="background:linear-gradient(135deg,#f1f1f1,#d5d0cc 60%,#b9a795)"></div>
  <div class="body"><div class="meta">04-09-2022 | By Mara Lindqvist</div><h4>Sed ut perspiciatis unde omnis</h4><p>Sed ut perspiciatis unde omnis iste natus error sit voluptatem accusantium doloremque</p></div>
</article>
<article class="abs news" style="left:442px">
  <div class="photo" role="img" aria-label="Colleagues meeting in a bright open office" style="background:linear-gradient(135deg,#dfe3e6,#b4bcc3 60%,#8c98a3)"></div>
  <div class="body"><div class="meta">04-09-2022 | By Mara Lindqvist</div><h4>Sed ut perspiciatis unde omnis</h4><p>Sed ut perspiciatis unde omnis iste natus error sit voluptatem accusantium doloremque</p></div>
</article>
<article class="abs news" style="left:772px">
  <div class="photo" role="img" aria-label="Programmer working at a desk with two monitors" style="background:linear-gradient(135deg,#2e3f3d,#3d4a48 55%,#8a6244)"></div>
  <div class="body"><div class="meta">04-09-2022 | By Mara Lindqvist</div><h4>Sed ut perspiciatis unde omnis</h4><p>Sed ut perspiciatis unde omnis iste natus error sit voluptatem accusantium doloremque</p></div>
</article>

<section class="abs contact">
  <h2 class="abs"><em>Contact</em> Us</h2>
  <p class="abs lead">Sed ut perspiciatis unde omnis iste natus error sit voluptatem accusantium doloremque laudantium.</p>
  <div class="abs info" style="top:227px">
    <svg viewBox="0 0 24 32"><path fill="#222832" d="M12 0C5.4 0 0 5.3 0 12c0 8.5 12 20 12 20s12-11.5 12-20C24 5.3 18.6 0 12 0zm0 17a5 5 0 1 1 0-10 5 5 0 0 1 0 10z"/></svg>
    <span>Velora, demo address comes here.</span>
  </div>
  <div class="abs info" style="top:291px">
    <svg viewBox="0 0 24 24"><path fill="#222832" d="M6.6 10.8c1.4 2.8 3.8 5.1 6.6 6.6l2.2-2.2c.3-.3.7-.4 1-.2 1.1.4 2.3.6 3.6.6.6 0 1 .4 1 1V20c0 .6-.4 1-1 1C10.6 21 3 13.4 3 4c0-.6.4-1 1-1h3.5c.6 0 1 .4 1 1 0 1.3.2 2.5.6 3.6.1.3 0 .7-.2 1z"/></svg>
    <span>+1 555-014-2290</span>
  </div>
  <div class="abs info" style="top:355px">
    <svg viewBox="0 0 28 22" style="height:24px"><path fill="#222832" d="M0 0h28v22H0z"/><path fill="none" stroke="#eef3fa" stroke-width="2.2" d="M1 2l13 10L27 2"/></svg>
    <span>info@velora.com</span>
  </div>
  <form class="abs form">
    <h5>Book An Appointment</h5>
    <div class="field" style="left:39px;top:71px;width:198px;height:45px">Name</div>
    <div class="field" style="left:242px;top:71px;width:200px;height:45px">Phone</div>
    <div class="field" style="left:39px;top:122px;width:198px;height:45px">Email</div>
    <div class="field" style="left:242px;top:122px;width:200px;height:45px">Date</div>
    <div class="field" style="left:39px;top:174px;width:403px;height:90px">Message</div>
    <a class="btn">Get a Quote</a>
  </form>
</section>

<footer class="abs footer">
  <div class="logo"><i></i>VELORA</div>
  <div class="foot-menu"><a>Home</a><a>About</a><a>Services</a><a>Our Project</a><a>Blog</a><a>Contact</a></div>
  <div class="copy">2022 Velora. All Rights Reserved.</div>
</footer>

</body>
</html>
```